Wordpress Design Project - Australian Solar Company wants to start FRESH!

About us

Bright Meadow are a renewable energy company based in Perth Australia, but we also have offices all over Asia. We specialise in offering renewable energy solutions (Solar PV Systems and LED Lighting) to residential and commercial customers.

Our current website: www.brightmeadowenergy.com.au

Our needs

This will be a replacement website as we are not happy with our current layout. We have an Australian company doing our SEO and they have recommended a new layout which we wish to go with.

We really want a professional and easy to navigate website that will assist in bringing in more enquiries and phone calls.

Content

We have all the content and will get the design winner to add this after we have chosen the design we like.
It is important that the call to actions are presented well and are visible these are things like the free quote form and our phone number.

The layout as we have advised has been based on SEO research so we wish it to be exactly the same unless otherwise stated.

Call to action

Our main objective of the new website is for people to come to the home page and see us as a professional and reliable company to deal with and enquire further.

We really want as many people as we can to convert to a lead. We want every person that comes to the website to enquire online or call us. We feel it is important to have a contact us/quote form on every page of the website.

Functional requirements

We have a chatterbook and vidstream account so links to these would be needed

Design assets

The logo needs to be displayed as shown in the website layout brief

Colours – we would like fresh, subdued colours that are professional and appealing to the eye. We ask that you do not take the colours from the logo.

Current website dislikes – the things we currently dislike about our current website is that it is hard to find information and there is no clear call to action. The colours are really unappealing as well as it looks cheap not professional.
The graphics that we require for the slider on the home page will have to be given after the winner is chosen but we want there to be three sliders on rotation

- Credibility builder (employee infront of solar panel) that encourages we use all our own employees not subcontractors
- Residential Slider – picture of a couple and solar panel system with a testimonial
- Commercial slider – picture of commercial system with “find out how you can install solar for free* at your business”

Design ideas

The website needs to be mobile friendly as well
It is going to be a total rebuild from the current website as our current website really isn’t working for us.

Target Market(s)

Target Audience

Our target audience are both residential and commercial clients
Residential – we want to attract home owners that are interested in reducing their electricity bill and helping the environment. Generally these people are between the ages of 28-50+ both male and female.

Commercial – We want to appeal to key decision makers within the commercial sphere. For example – CEOs, Company Directors, Operation managers and business owners of any industry. These people will be interested in reducing their electricity bills and creating a clean green image for their business.
Our target audience will generally come to our website to get information and enquire for a quote/ product information.

Industry/Entity Type

Residential

Requirements
Must have
• MUST BE LAID OUT LIKE THIS:

http://www.pagevaultdocs.com/doc/482937105/Website-Layout

Must have Enquire Now forms on every page that read:

Name
Phone Number
How did you hear about us
Message

```html
<!DOCTYPE html>
<html lang="en">
<head>
<meta charset="utf-8">
<title>Bright Meadow – Home</title>
<link href="https://fonts.googleapis.com/css2?family=Source+Sans+3:wght@400;600;700&family=PT+Sans+Narrow:wght@400;700&display=swap" rel="stylesheet">
<style>
:root{
  --green:#0c8a3c;
  --orange:#f4a81c;
  --nav-dark:#141414;
  --text:#333;
  --text-soft:#666;
  --footer-text:#e6e6e6;
}
*{box-sizing:border-box;margin:0;padding:0}
html,body{width:856px;height:1200px;overflow:hidden}
body{position:relative;background:#fff;font-family:"Source Sans 3",sans-serif;color:var(--text)}

/* header */
.site-header{position:absolute;left:0;top:0;width:856px;height:119px;
  background:linear-gradient(90deg,#fff 0%,#f3f9e6 30%,#eef7dc 60%,#d6ecb4 100%)}
.brand{position:absolute;left:80px;top:50px;display:flex;align-items:center;gap:8px}
.brand-mark{width:26px;height:26px;border-radius:50%;background:var(--orange)}
.brand-name{font-weight:700;font-size:24px;color:var(--green)}
.tagline{position:absolute;left:152px;top:102px;font-size:8px;font-style:italic;color:#333}
.header-phone{position:absolute;left:572px;top:12px;display:flex;align-items:center;gap:4px;font-size:22px;color:#222}
.header-mail{position:absolute;left:578px;top:50px;display:flex;align-items:center;gap:10px;font-size:12px;color:#333}
.social-badge{position:absolute;left:807px;top:0;width:28px;height:27px;border-radius:0 0 8px 8px;background:#3c63a8}
.main-nav{position:absolute;left:414px;top:89px;display:flex;gap:2px}
.main-nav a{display:block;height:28px;line-height:30px;padding:0 12px;font-size:11.5px;color:#fff;text-decoration:none;
  background:var(--nav-dark);border-radius:3px 3px 0 0}
.main-nav a.is-active{background:var(--orange)}

/* hero */
.hero{position:absolute;left:0;top:119px;width:856px;height:338px;
  background:linear-gradient(160deg,#6fb7e8 0%,#3d8fd0 35%,#1f4f9a 70%,#2d63b0 100%)}
.hero-shadow{position:absolute;left:20px;top:457px;width:816px;height:8px;border-radius:50%;
  background:radial-gradient(ellipse at center,rgba(0,0,0,.25),transparent 70%)}
.hero-caption{position:absolute;left:0;top:227px;width:358px;height:107px;background:rgba(10,25,45,.72);color:#fff;padding:14px 0 0 73px}
.hero-caption h2{font-family:"PT Sans Narrow",sans-serif;font-weight:700;font-size:22px;margin-bottom:5px}
.hero-caption p{font-size:13.5px;line-height:20px;width:240px}
.slide-arrow{position:absolute;top:258px;width:25px;height:25px;border-radius:50%;background:rgba(255,255,255,.55)}

/* quote form */
.quote-panel{position:absolute;left:567px;top:120px;width:212px;height:225px;
  background:linear-gradient(180deg,rgba(42,155,134,.92),rgba(60,170,120,.85));padding:14px 14px 0}
.quote-title{display:flex;align-items:center;gap:12px;font-family:"PT Sans Narrow",sans-serif;font-weight:700;font-size:17px;color:#fff;margin-left:-6px}
.quote-form{margin-top:14px}
.quote-field{display:block;width:184px;height:22px;margin-bottom:6px;border:1px solid #d6d6d6;border-radius:2px;background:#fff;
  font:italic 8.5px "Source Sans 3",sans-serif;color:#888;padding:0 12px;line-height:22px}
.quote-field.is-message{height:36px;line-height:48px}
.quote-submit{position:absolute;left:132px;top:190px;width:67px;height:23px;border-radius:12px;border:1px solid #fff;
  background:var(--orange);color:#fff;font:italic 700 12px "PT Sans Narrow",sans-serif;line-height:21px;text-align:center}

/* service cards */
.service-card{position:absolute;top:500px;width:218px;height:228px;border:1px solid #d8d8d8;border-radius:2px;background:#fff;padding:8px}
.service-card::after{content:"";position:absolute;left:16px;right:16px;bottom:-9px;height:6px;border-radius:50%;
  background:radial-gradient(ellipse at center,rgba(0,0,0,.25),transparent 70%)}
.card-media{position:relative;height:124px}
.card-media .label{position:absolute;left:0;right:0;bottom:0;height:30px;background:rgba(20,20,20,.65);color:#fff;
  font-family:"PT Sans Narrow",sans-serif;font-size:15px;line-height:30px;padding-left:16px}
.card-text{font-size:9.2px;line-height:13.4px;color:var(--text-soft);text-align:justify;padding:7px 6px 0}
.card-button{position:absolute;left:8px;right:8px;bottom:7px;height:21px;background:var(--green);border-radius:2px;
  color:#fff;font-size:12px;line-height:21px;text-align:right;padding-right:12px}
.card-button::before{content:"";display:inline-block;width:9px;height:9px;border-radius:50%;background:var(--orange);margin-right:6px;vertical-align:-1px}

/* welcome + testimonials */
.welcome{position:absolute;left:78px;top:766px;width:368px}
.welcome h1{font-weight:400;font-size:20px;color:#222;letter-spacing:.2px}
.welcome h1 span{color:var(--green)}
.welcome .lead{font-weight:700;font-size:10px;color:#222;margin:10px 0 6px}
.welcome p.body{font-size:9.2px;line-height:15px;color:#444;text-align:justify}
.learn-more{position:absolute;left:378px;top:932px;width:68px;height:27px;background:var(--green);color:#fff;
  font-family:"PT Sans Narrow",sans-serif;font-size:12px;line-height:27px;text-align:center}
.testimonials{position:absolute;left:485px;top:764px}
.testimonials h2{font-weight:400;font-size:20px;color:var(--green)}
.video{position:absolute;left:485px;top:801px;width:301px;height:156px;background:#111;padding:3px}
.video-frame{height:133px;background:linear-gradient(90deg,#c9d1d6 0%,#b9a392 45%,#d6dde1 100%)}
.video-play{position:absolute;left:141px;top:62px;width:30px;height:21px;background:#111;border-radius:3px}
.video-bar{position:absolute;left:3px;right:3px;bottom:3px;height:14px;background:#1a1a1a}
.video-progress{position:absolute;left:3px;right:3px;bottom:17px;height:3px;background:#555}
.video-progress::before{content:"";position:absolute;left:0;top:0;width:68px;height:3px;background:#c00}

/* footer */
.site-footer{position:absolute;left:0;top:993px;width:856px;height:207px;background:linear-gradient(180deg,#565656 0,#3b3b3b 6px,#3a3a3a 100%);color:var(--footer-text)}
.footer-col{position:absolute;top:22px;width:170px}
.footer-col h3{font-weight:400;font-size:14.5px;color:#fff;margin-bottom:8px}
.footer-col p{font-size:8.8px;line-height:13.4px;text-align:justify;color:#ddd}
.footer-list{list-style:none;font-size:8.8px;line-height:20px;color:#eee;margin-top:-3px}
.footer-list li::before{content:"›";margin:0 8px 0 6px}
.footer-button{display:block;margin-top:12px;height:25px;background:var(--orange);border-radius:2px;color:#fff;font-size:13px;line-height:25px;text-align:center}
.contact-info p{text-align:left}
.social-row{position:absolute;left:44px;top:176px;display:flex;gap:9px}
.social-row span{width:18px;height:18px;border-radius:2px}
.copyright{position:absolute;right:35px;top:174px;font-size:9px;color:#eee}
</style>
</head>
<body>

<header class="site-header">
  <div class="brand">
    <span class="brand-mark"></span>
    <span class="brand-name">Bright Meadow</span>
  </div>
  <div class="tagline">"Clean Power For Every Rooftop"</div>

  <div class="header-phone">
    <svg width="22" height="20" viewBox="0 0 22 20" aria-hidden="true"><path d="M4 2 L8 2 L9 6 L7 8 Q10 13 14 14 L16 12 L20 13 L20 17 Q18 19 15 18 Q6 15 3 6 Q2 3 4 2Z" fill="#222"/></svg>
    <span>(08) 6104 2290</span>
  </div>
  <div class="header-mail">
    <svg width="18" height="13" viewBox="0 0 18 13" aria-hidden="true"><rect x="0.5" y="0.5" width="17" height="12" fill="#333"/><path d="M1 1 L9 8 L17 1" stroke="#eee" fill="none"/></svg>
    <span>sales@brightmeadowenergy.com.au</span>
  </div>
  <div class="social-badge" aria-label="chatterbook"></div>

  <nav class="main-nav">
    <a class="is-active">HOME</a>
    <a>ABOUT US</a>
    <a>PRODUCTS</a>
    <a>WHY BRIGHT MEADOW</a>
    <a>CONTACT</a>
  </nav>
</header>

<section class="hero" role="img" aria-label="Close view of a rooftop solar panel array under a bright blue sky"></section>
<div class="hero-shadow"></div>
<div class="hero-caption">
  <h2>Solar Photovoltaic</h2>
  <p>All our home Solar Panels are of high quality with long lifetime guarantees.</p>
</div>
<div class="slide-arrow" style="left:17px">
  <svg width="25" height="25" viewBox="0 0 25 25" aria-hidden="true"><path d="M18 12.5 H8 M12 8 L7.5 12.5 L12 17" stroke="#444" stroke-width="3" fill="none"/></svg>
</div>
<div class="slide-arrow" style="left:787px">
  <svg width="25" height="25" viewBox="0 0 25 25" aria-hidden="true"><path d="M7 12.5 H17 M13 8 L17.5 12.5 L13 17" stroke="#3d8fd0" stroke-width="3" fill="none"/></svg>
</div>

<aside class="quote-panel">
  <div class="quote-title">
    <svg width="32" height="30" viewBox="0 0 32 30" aria-hidden="true"><path d="M2 14 L16 4 L30 14 L30 28 L2 28Z" fill="#fff"/><path d="M2 14 L16 22 L30 14" stroke="#bbb" fill="none"/></svg>
    <span>QUOTE ONLINE</span>
  </div>
  <div class="quote-form">
    <span class="quote-field">First Name</span>
    <span class="quote-field">Phone Number</span>
    <span class="quote-field">How did you hear about us</span>
    <span class="quote-field is-message">Message</span>
  </div>
  <span class="quote-submit">SUBMIT</span>
</aside>

<article class="service-card" style="left:70px">
  <div class="card-media" role="img" aria-label="House roof fitted with residential solar panels" style="background:linear-gradient(180deg,#9cc2e6 0%,#4b6a8f 45%,#283a5c 100%)">
    <div class="label">Residential Solar Power</div>
  </div>
  <p class="card-text">Sed ut perspiciatis unde omnis iste natus error doloremque laudantium, totam rem aperiam, eaque ipsa quae ab illo inventor. Nemo enim ipsam voluptatem quia voluptas.</p>
  <div class="card-button">Read More</div>
</article>
<article class="service-card" style="left:322px">
  <div class="card-media" role="img" aria-label="Large commercial solar panel field" style="background:linear-gradient(180deg,#a9bccf 0%,#7b8ea4 40%,#2f4463 100%)">
    <div class="label">Commercial Solar Power</div>
  </div>
  <p class="card-text">Sed ut perspiciatis unde omnis iste natus error doloremque laudantium, totam rem aperiam, eaque ipsa quae ab illo inventor. Nemo enim ipsam voluptatem quia voluptas.</p>
  <div class="card-button">Read More</div>
</article>
<article class="service-card" style="left:573px">
  <div class="card-media" role="img" aria-label="Colourful LED light bulbs glowing" style="background:linear-gradient(135deg,#2a1b5c 0%,#7a2a8a 40%,#c2304a 70%,#2b3f9c 100%)">
    <div class="label">LED Lighting</div>
  </div>
  <p class="card-text">Sed ut perspiciatis unde omnis iste natus error doloremque laudantium, totam rem aperiam, eaque ipsa quae ab illo inventor. Nemo enim ipsam voluptatem quia voluptas.</p>
  <div class="card-button">Read More</div>
</article>

<section class="welcome">
  <h1>WELCOME TO <span>BRIGHT MEADOW</span></h1>
  <p class="lead">Mauris vel lacus vitae felis vestibulum volutpat. Etiam est nunc, venisl.</p>
  <p class="body">Sed ut perspiciatis unde omnis iste natus error sit voluptatem accusantium doloremque laudantium, totam rem aperiam, eaque ipsa quae ab illo inventore veritatis et quasi architecto beatae vitae dicta sunt explicabo. Nemo enim ipsam voluptatem quia voluptas sit aspernatur aut odit aut fugit, sed quia consequuntur magni dolores eos qui ratione voluptatem sequi nesciunt. Neque porro quisquam est, qui dolorem ipsum quia dolor sit amet.s sit aspernatur aut odit aut fugit, sed quia consequuntur magni dolores eos qui ratione voluptatem sequi nesciunt.</p>
</section>
<div class="learn-more">learn more</div>

<section class="testimonials"><h2>TESTIMONIALS</h2></section>
<div class="video">
  <div class="video-frame" role="img" aria-label="Video still of a customer giving a testimonial in an office"></div>
  <div class="video-play">
    <svg width="30" height="21" viewBox="0 0 30 21" aria-hidden="true"><path d="M11 5 L20 10.5 L11 16Z" fill="#fff"/></svg>
  </div>
  <div class="video-progress"></div>
  <div class="video-bar"></div>
</div>

<footer class="site-footer">
  <div class="footer-col" style="left:33px">
    <h3>Primary/Product Services</h3>
    <ul class="footer-list">
      <li>Electrical Contracting Services</li>
      <li>Building Services</li>
      <li>Electrical Network and Structure Cabling</li>
      <li>Refrigeration Systems</li>
    </ul>
  </div>
  <div class="footer-col" style="left:259px">
    <h3>Membership</h3>
    <p>Sed ut perspiciatis unde omnis iste natus usantium doloremque laudantium, totam invenuuntur magni dolores ratione voluptatem sequi nesciunt.</p>
    <span class="footer-button" style="width:106px">Join Us</span>
  </div>
  <div class="footer-col" style="left:469px">
    <h3>Request Quotation</h3>
    <p>Sed ut perspiciatis unde omnis iste natus usantium doloremque laudantium, totam invenuuntur magni dolores ratione voluptatem sequi nesciunt.</p>
    <span class="footer-button" style="width:133px">Request Quotation</span>
  </div>
  <div class="footer-col contact-info" style="left:679px">
    <h3>Contact Info</h3>
    <p>U4 12-14 Kestrel Road<br>Willow Park, WA 6160</p>
    <p style="margin-top:8px">Phone: (08) 6104 2290<br>Fax: (08) 6104 2291<br>Email: sales@brightmeadowenergy.com.au</p>
  </div>

  <div class="social-row">
    <span style="background:#3c63a8" aria-label="chatterbook"></span>
    <span style="background:#35a9e0"></span>
    <span style="background:#5a5a5a"></span>
    <span style="background:#f39a1e"></span>
    <span style="background:#c9262c" aria-label="vidstream"></span>
  </div>
  <div class="copyright">© 2013 brightmeadowenergy, All rights reserved</div>
</footer>

</body>
</html>
```